NZ First of it's kind solutions directory and marketplace for busy Mums needs a business card design

We need a business card design for our new nationwide business in NZ (long term plans to go global). We provide solutions to the everyday challenges that busy Mums face by connecting them with quality communities and suppliers of carefully selected, relevant products and services. We sell direct via our online marketplace. The final design should communicate our values of inclusivity, quality and smart solutions. Colours should incorporate our logo colour palette of #477077 and #6ba8b2. Our website is at https://www.brightnestmums.example

Target Market(s)

busy Mums, Age 28 – 50, female, income over $100K, location main centres NZ primarily but NZ wide. Is likely juggling work or career with a young family. Probably had hobbies which have fallen by the wayside.
-Wants to succeed in her chosen career without compromising on family life
-to successfully juggle her career without feeling like she is compromising her children
- Is time poor, something always has to give and it’s generally her health (she’ll stay up late, get stressed)
- probably ex corporate or professional career. Has discretional income

Industry/Entity Type

Business

Contact Information for Business Card

Lena Forbisher, Founder, BrightNestMums.example (Strapline Tap; Gather; Sorted), 47 Kowhai Terrace, Ellerslie, Auckland 1051, New Zealand. Mob: 021 483 517 Ph: +64 (0)9 571 4860

Font styles to use
Other font styles liked:
• Raleway, and/or Architects Daughter

Colors
00a990
33b8a4
86cfc6
cfeae6

Requirements
Must have
• the above details, streamline. the logo and colours associated with those logos
Should not have
• foil or metallic colours

```html
<!DOCTYPE html>
<html lang="en">
<head>
<meta charset="utf-8">
<title>BrightNestMums – Business Card</title>
<link rel="stylesheet" href="https://fonts.googleapis.com/css2?family=Architects+Daughter&family=Raleway:wght@400;500;600;700;800&display=swap">
<style>
  :root {
    --teal-dark: #477077;
    --teal-light: #6ba8b2;
    --teal-rule: #2f8a8c;
    --ink-soft: #5d6a6c;
    --paper: #ffffff;
    --backdrop: #e8ecec;
  }
  * { box-sizing: border-box; margin: 0; padding: 0; }
  html, body { width: 1200px; height: 900px; overflow: hidden; }
  body {
    background: var(--backdrop);
    font-family: "Raleway", sans-serif;
    position: relative;
  }
  .card {
    position: absolute;
    width: 630px;
    height: 360px;
    border-radius: 4px;
    box-shadow: 0 10px 28px rgba(0,0,0,0.18);
    overflow: hidden;
  }

  /* Front */
  .card-front {
    left: 90px; top: 70px;
    background: var(--teal-light);
  }
  .front-brand {
    position: absolute;
    left: 150px; top: 130px;
    display: flex; align-items: center; gap: 22px;
  }
  .brand-dot {
    width: 64px; height: 64px; border-radius: 50%;
    background: var(--paper);
    flex: none;
  }
  .front-name {
    font-weight: 800;
    font-size: 40px;
    letter-spacing: -0.5px;
    color: var(--paper);
  }
  .front-url {
    position: absolute;
    left: 236px; top: 196px;
    font-size: 15px;
    font-weight: 500;
    color: var(--paper);
    letter-spacing: 0.3px;
  }

  /* Back */
  .card-back {
    left: 480px; top: 470px;
    background: var(--paper);
  }
  .back-brand {
    position: absolute;
    right: 34px; top: 70px;
    display: flex; align-items: center; gap: 12px;
  }
  .back-brand .brand-dot {
    width: 30px; height: 30px;
    background: var(--teal-dark);
  }
  .back-name {
    font-weight: 800;
    font-size: 36px;
    letter-spacing: -0.5px;
    color: var(--teal-dark);
  }
  .rule {
    position: absolute;
    height: 3px;
    background: var(--teal-rule);
  }
  .rule-main { left: 232px; right: 0; top: 178px; }
  .rule-left { left: 0; width: 30px; top: 200px; }
  .strapline {
    position: absolute;
    right: 34px; top: 124px;
    font-family: "Architects Daughter", cursive;
    font-size: 19px;
    color: var(--teal-light);
  }
  .address {
    position: absolute;
    right: 34px; top: 196px;
    text-align: right;
    font-size: 14px;
    line-height: 1.4;
    color: var(--ink-soft);
  }
  .person {
    position: absolute;
    left: 40px; top: 160px;
  }
  .person-name {
    font-weight: 800;
    font-size: 18px;
    letter-spacing: 0.5px;
    color: var(--teal-dark);
    text-transform: uppercase;
  }
  .person-role {
    font-size: 14px;
    color: var(--ink-soft);
  }
  .contacts {
    position: absolute;
    left: 40px; bottom: 34px;
    list-style: none;
    font-size: 14px;
    line-height: 1.55;
    color: var(--ink-soft);
  }
  .contacts li { display: flex; align-items: center; gap: 12px; }
  .contacts svg { width: 13px; height: 13px; fill: var(--teal-rule); flex: none; }
</style>
</head>
<body>

  <section class="card card-front" aria-label="Card front">
    <div class="front-brand">
      <span class="brand-dot"></span>
      <span class="front-name">BrightNestMums</span>
    </div>
    <div class="front-url">www.BrightNestMums.example</div>
  </section>

  <section class="card card-back" aria-label="Card back">
    <div class="back-brand">
      <span class="brand-dot"></span>
      <span class="back-name">BrightNestMums</span>
    </div>
    <div class="strapline">Strapline Tap, Gather, Sorted</div>
    <div class="rule rule-main"></div>
    <div class="rule rule-left"></div>

    <div class="person">
      <div class="person-name">Lena Forbisher</div>
      <div class="person-role">Founder</div>
    </div>

    <address class="address" style="font-style:normal">
      47 Kowhai Terrace, Ellerslie<br>
      Auckland 1051, NZ
    </address>

    <ul class="contacts">
      <li>
        <svg viewBox="0 0 24 24" aria-hidden="true"><path d="M6.6 10.8a15.1 15.1 0 0 0 6.6 6.6l2.2-2.2a1 1 0 0 1 1-.25 11.4 11.4 0 0 0 3.6.57 1 1 0 0 1 1 1V20a1 1 0 0 1-1 1A17 17 0 0 1 3 4a1 1 0 0 1 1-1h3.5a1 1 0 0 1 1 1c0 1.25.2 2.45.57 3.57a1 1 0 0 1-.25 1z"/></svg>
        +64 (0)9 571 4860
      </li>
      <li>
        <svg viewBox="0 0 24 24" aria-hidden="true"><path d="M7 1h10a2 2 0 0 1 2 2v18a2 2 0 0 1-2 2H7a2 2 0 0 1-2-2V3a2 2 0 0 1 2-2zm0 3v14h10V4zm5 15.2a1.2 1.2 0 1 0 0 2.4 1.2 1.2 0 0 0 0-2.4z"/></svg>
        +64 021 483 517
      </li>
      <li>
        <svg viewBox="0 0 24 24" aria-hidden="true"><path d="M2 5h20v14H2zm2 2v.5l8 5 8-5V7zm0 2.9V17h16V9.9l-8 5z"/></svg>
        hello@brightnestmums.example
      </li>
    </ul>
  </section>

</body>
</html>
```